Real Estate stationery - need an interesting, eye catching design

I need a letterhead and #10 envelope design in the same theme.
I am looking for an interesting, eye catching design that would stand out in the crowd. I am in the real estate business(which is very competitive) in Florida so standing out and being different is very important to me.
Marguerite(Rita) Delacourt (name), RealtorĀ® (title), 352-608-2147 (cell), bayviewritahomes@quellmail.com (email), www.bayviewritahomes.com(website), 915 Calloway Creek Blvd.,Ste. 3140, Longwood, FL 32779 (business address)

```html
<!DOCTYPE html>
<html lang="en">
<head>
<meta charset="utf-8">
<title>Keystone Harbor Realty — Letterhead and Envelope</title>
<link href="https://fonts.googleapis.com/css2?family=Raleway:wght@300;400&family=Roboto:wght@400&display=swap" rel="stylesheet">
<style>
  :root {
    --backdrop: #dcdcdc;
    --paper: #f5f5f5;
    --paper-edge: #fdfdfd;
    --band-grey: #7b7c80;
    --accent-brown: #7c5a26;
    --ink: #4a4a4a;
    --ink-soft: #6a6a6a;
    --white: #ffffff;
  }
  * { box-sizing: border-box; margin: 0; padding: 0; }
  html, body { width: 1200px; height: 843px; overflow: hidden; }
  body {
    background: var(--backdrop);
    font-family: "Raleway", sans-serif;
    color: var(--ink);
    position: relative;
  }
  .sheet {
    position: absolute;
    background: linear-gradient(90deg, var(--paper-edge), var(--paper));
    box-shadow: 0 2px 14px rgba(0,0,0,0.22);
    overflow: hidden;
  }

  /* Letterhead */
  .letterhead { left: 74px; top: 61px; width: 508px; height: 716px; }
  .brand-name {
    position: absolute;
    font-family: "Raleway", sans-serif;
    font-weight: 400;
    color: var(--accent-brown);
    letter-spacing: 0.02em;
    white-space: nowrap;
  }
  .letterhead .brand-name { left: 45px; top: 78px; font-size: 15px; }
  .contact-block {
    position: absolute; left: 343px; top: 62px;
    border-left: 1px solid #bdbdbd;
    padding-left: 11px;
    font-family: "Roboto", sans-serif;
    font-size: 7.2px; line-height: 9px; color: var(--ink);
  }
  .contact-line { display: flex; align-items: center; gap: 4px; margin-top: 1px; }
  .contact-line svg { width: 6px; height: 6px; fill: var(--accent-brown); }
  .contact-block .address { margin-bottom: 4px; }
  .salutation { position: absolute; left: 45px; top: 200px; font-size: 13px; font-weight: 300; color: #3a3a3a; }
  .letter-body {
    position: absolute; left: 45px; top: 237px; width: 422px;
    font-size: 7.6px; line-height: 11px; font-weight: 300; color: var(--ink-soft);
    text-align: justify;
  }
  .letter-body p { margin-bottom: 11px; }
  .closing { position: absolute; left: 45px; top: 473px; font-size: 7.2px; font-weight: 300; color: var(--ink-soft); }
  .signature { position: absolute; left: 40px; top: 498px; width: 94px; height: 38px; background: linear-gradient(90deg, #d6d6d6, #e6e6e6); border-radius: 3px; }

  .footer-band { position: absolute; left: 0; height: 24px; width: 100%; }
  .footer-band .grey { position: absolute; left: 0; top: 0; height: 22px; background: var(--band-grey); }
  .footer-band .brown { position: absolute; right: 0; bottom: 0; background: var(--accent-brown); }
  .footer-band .web {
    position: absolute; top: 0; line-height: 22px;
    font-family: "Roboto", sans-serif; font-size: 7.5px; letter-spacing: 0.2em; color: var(--white);
  }
  .letterhead .footer-band { top: 677px; }
  .letterhead .footer-band .grey { width: 400px; }
  .letterhead .footer-band .brown { width: 52px; height: 15px; }
  .letterhead .footer-band .web { left: 125px; }

  /* Envelope back */
  .envelope-back { left: 621px; top: 275px; width: 512px; height: 233px; }
  .flap { position: absolute; left: 0; top: 0; width: 512px; height: 74px; }
  .envelope-back .brand-name { left: 0; width: 512px; text-align: center; top: 30px; font-size: 13px; color: var(--white); }

  /* Envelope front */
  .envelope-front { left: 621px; top: 543px; width: 512px; height: 233px; }
  .envelope-front .brand-name { left: 25px; top: 42px; font-size: 12.5px; }
  .return-address {
    position: absolute; left: 22px; top: 72px; width: 122px; text-align: center;
    font-family: "Roboto", sans-serif; font-size: 7px; line-height: 9px; color: #333;
  }
  .envelope-front .footer-band { top: 196px; }
  .envelope-front .footer-band .grey { width: 395px; }
  .envelope-front .footer-band .brown { width: 52px; height: 15px; }
  .envelope-front .footer-band .web { left: 120px; }
</style>
</head>
<body>

<section class="sheet letterhead">
  <div class="brand-name">Keystone Harbor Realty</div>
  <div class="contact-block">
    <div class="address">915 Calloway Creek Blvd.,<br>Ste. 3140<br>Marlow Springs, FL 34612</div>
    <div class="contact-line">
      <svg viewBox="0 0 6 6"><rect x="1.5" y="0" width="3" height="6" rx="0.6"/></svg>352-608-2147
    </div>
    <div class="contact-line">
      <svg viewBox="0 0 6 6"><rect x="0" y="1" width="6" height="4" rx="0.4"/></svg>bayviewritahomes@quellmail.com
    </div>
  </div>

  <p class="salutation">Dear Mr. Hollis,</p>
  <div class="letter-body">
    <p>Lorem ipsum dolor sit amet, consectetur adipiscing elit. Donec orci purus, luctus vitae dignissim eu, iaculis sed purus. Vivamus faucibus, ipsum nec aliquet viverra, leo mauris condimentum ligula, sit amet sagittis enim ligula quis arcu. Nam egestas tortor id nisi porttitor mattis. In tortor ante, ultricies in suscipit a, tempus non massa. Vivamus et auctor mi. Fusce vel massa nulla. Phasellus nec eros mauris, et scelerisque orci.</p>
    <p>Donec malesuada orci vitae nulla accumsan porta a id massa. Quisque accumsan iaculis magna sit amet fringilla. Maecenas consequat, magna eget tincidunt semper, odio nibh rutrum mi, id feugiat ante nisi eu risus. Vestibulum nunc orci, rhoncus a placerat in, ultricies in mi. Cras mattis varius eros, vel fringilla nisi suscipit eget. Quisque scelerisque sagittis nulla at porttitor.</p>
    <p>Sed id augue vitae urna euismod commodo aliquet a quam. Pellentesque arcu velit, cursus et malesuada ut, consequat et diam. Nullam erat sem, rhoncus id ullamcorper vitae, rhoncus et arcu. In ultricies ultricies nulla, ut rutrum nisi iaculis at. Donec eu magna a metus ornare faucibus. Fusce aliquet faucibus ultricies. Morbi semper, est id tincidunt gravida, sem arcu adipiscing lacus, ac bibendum nulla leo eu purus. Quisque nec diam sed risus consectetur accumsan quis quis nibh. Vestibulum id purus lorem.</p>
    <p>It is a long established fact that a reader will be distracted by the readable content of a page when looking at its layout. The point of using Lorem Ipsum is that it has a more-or-less normal distribution of letters, as opposed to using 'Content here, content here', making it look like readable English. Many desktop publishing packages</p>
  </div>
  <p class="closing">Sincerely,</p>
  <div class="signature" role="img" aria-label="Handwritten signature of Owen Hollis"></div>

  <div class="footer-band">
    <div class="grey"></div>
    <div class="brown"></div>
    <span class="web">www.bayviewritahomes.com</span>
  </div>
</section>

<section class="sheet envelope-back">
  <svg class="flap" viewBox="0 0 512 74" aria-hidden="true">
    <path d="M0 0 H512 L504 28 Q496 74 460 74 H50 Q18 74 10 34 Z" fill="#7b7c80"/>
  </svg>
  <div class="brand-name">Keystone Harbor Realty</div>
</section>

<section class="sheet envelope-front">
  <div class="brand-name">Keystone Harbor Realty</div>
  <div class="return-address">915 Calloway Creek Blvd.,Ste. 3140<br>Marlow Springs, FL 34612</div>
  <div class="footer-band">
    <div class="grey"></div>
    <div class="brown"></div>
    <span class="web">www.bayviewritahomes.com</span>
  </div>
</section>

</body>
</html>
```